Kelvara Pane Works Business Card

We need a business card design that is suitable for a Glazing Business. We Specialize in Repairing broken windows and doors and are a 24hr on call service. We manufacture Shower screens, Fly screens, Wardrobe doors, Security doors and grilles + mirrors. We stock a variety of mesh including Standard mesh, Pet resistant mesh, Tressmet & Clearweft. We would like to use a combination of Light Blue, Dark Blue, Black & White with perhaps a picture of glass breaking.

Industry/Entity Type

Business

Contact Information for Business Card

Narooma Glass Service60B Glasshouse Rocks RdNarooma NSW 2546PH / FAX - 02 44765210MOB - 0419682350 Andrewemail - kelvarapane@fenmail.example

Font styles to use
Serif

Colors
34a7d8
0255a3
ffffff

Requirements
Must have
• logo with picture of broken or cracked glass

```html
<!DOCTYPE html>
<html lang="en">
<head>
<meta charset="utf-8">
<title>Kelvara Pane Works Business Card</title>
<link rel="stylesheet" href="https://fonts.googleapis.com/css2?family=Marcellus&family=Saira:wght@300;400&display=swap">
<style>
  :root {
    --page: #e8e5e0;
    --card-black: #0b0d11;
    --card-charcoal: #1c2129;
    --glass-blue: #2f3a4a;
    --brand-blue: #7fc3e6;
    --band: #5a6d8c;
    --band-edge: #44546e;
    --ink-light: #f2f5f8;
    --rule: rgba(190, 205, 225, 0.45);
  }
  * { box-sizing: border-box; margin: 0; padding: 0; }
  html, body {
    width: 1200px;
    height: 1023px;
    overflow: hidden;
    background: var(--page);
    font-family: "Saira", "Helvetica Neue", Arial, sans-serif;
  }
  .business-card {
    position: absolute;
    left: 100px;
    top: 226px;
    width: 1000px;
    height: 571px;
    background: var(--card-black);
    box-shadow: 0 18px 40px rgba(0, 0, 0, 0.25);
    overflow: hidden;
  }
  .glass-texture {
    position: absolute;
    inset: 0;
    background:
      radial-gradient(ellipse at 30% 55%, var(--glass-blue) 0%, transparent 50%),
      radial-gradient(ellipse at 78% 30%, var(--card-charcoal) 0%, transparent 55%),
      linear-gradient(135deg, var(--card-charcoal) 0%, var(--card-black) 60%, #15191f 100%);
  }
  .card-divider {
    position: absolute;
    left: 500px;
    top: 40px;
    width: 1px;
    height: 427px;
    background: var(--rule);
  }
  .logo-block {
    position: absolute;
    left: 0;
    top: 0;
    width: 500px;
    height: 507px;
    display: flex;
    align-items: center;
    justify-content: center;
  }
  .logo-burst {
    position: absolute;
    left: 40px;
    top: 50px;
    width: 420px;
    height: 400px;
    border-radius: 50%;
    background: radial-gradient(circle,
      rgba(225, 236, 248, 0.16) 0%,
      rgba(235, 242, 250, 0.5) 38%,
      rgba(235, 242, 250, 0.22) 55%,
      transparent 70%);
  }
  .brand-name {
    position: relative;
    text-align: center;
    color: var(--brand-blue);
    font-family: "Marcellus", Georgia, serif;
    font-weight: 400;
    line-height: 1;
  }
  .brand-name .brand-main {
    display: block;
    font-size: 84px;
    letter-spacing: 1px;
  }
  .brand-name .brand-sub {
    display: block;
    margin-top: 12px;
    font-size: 30px;
    letter-spacing: 2px;
  }
  .contact-list {
    position: absolute;
    left: 548px;
    top: 70px;
    list-style: none;
    color: var(--ink-light);
    font-size: 25px;
    font-weight: 300;
    line-height: 1.45;
  }
  .contact-list li {
    display: flex;
    align-items: flex-start;
    gap: 16px;
  }
  .contact-icon {
    flex: none;
    width: 22px;
    height: 22px;
    margin-top: 9px;
  }
  .service-band {
    position: absolute;
    left: 0;
    bottom: 0;
    width: 1000px;
    height: 64px;
    background: var(--band);
    border-top: 3px solid var(--band-edge);
    display: flex;
    align-items: center;
    justify-content: center;
    list-style: none;
    color: var(--ink-light);
    font-size: 24px;
    font-weight: 300;
    letter-spacing: 0.5px;
  }
  .service-band li { padding: 0 18px; }
  .service-band li + li { border-left: 1px solid rgba(242, 245, 248, 0.55); }
</style>
</head>
<body>
  <article class="business-card">
    <div class="glass-texture" role="img" aria-label="Dark shattered glass texture across the card"></div>

    <div class="logo-block">
      <div class="logo-burst" role="img" aria-label="Broken glass logo: white cracked glass burst radiating behind the business name"></div>
      <h1 class="brand-name">
        <span class="brand-main">Kelvara</span>
        <span class="brand-sub">Pane Works</span>
      </h1>
    </div>

    <div class="card-divider"></div>

    <ul class="contact-list">
      <li>
        <svg class="contact-icon" viewBox="0 0 24 24" aria-hidden="true"><circle cx="12" cy="12" r="11" fill="none" stroke="#f2f5f8" stroke-width="2"/><rect x="8.5" y="5.5" width="7" height="13" rx="1.5" fill="#f2f5f8"/></svg>
        <span>0419682350 Malcolm</span>
      </li>
      <li>
        <svg class="contact-icon" viewBox="0 0 24 24" aria-hidden="true"><circle cx="12" cy="12" r="11" fill="#f2f5f8"/><path d="M7 9c0-1 1-2 2-2h6c1 0 2 1 2 2v1H7z M8 11h8l1 6H7z" fill="#0b0d11"/></svg>
        <span>02 48931067</span>
      </li>
      <li>
        <svg class="contact-icon" viewBox="0 0 24 24" aria-hidden="true"><rect x="2" y="5" width="20" height="14" fill="#f2f5f8"/><path d="M2 5l10 8 10-8" fill="none" stroke="#0b0d11" stroke-width="2"/></svg>
        <span>kelvarapane@fenmail.example</span>
      </li>
      <li>
        <svg class="contact-icon" viewBox="0 0 24 24" aria-hidden="true"><path d="M12 3l10 9h-3v8h-5v-5h-4v5H5v-8H2z" fill="#f2f5f8"/></svg>
        <span>17C Tindale Ridge Rd.<br>Kelvara NSW 2631</span>
      </li>
    </ul>

    <ul class="service-band">
      <li>Shower screens</li>
      <li>Security doors</li>
      <li>wardrobe doors</li>
      <li>fly screens</li>
      <li>Clearsheet</li>
    </ul>
  </article>
</body>
</html>
```